Wellness Coach/Personal trainer needs wordpress site/blog with ecommerce capable membership area

We need a WordPress design for FitPennyCoach.com. This is a blog about wellness, weight loss, and health related topics. Design logo will be provided to the winner.

A great site with a design that we would like to emulate are http://qv4.example. The design should be simple, clean, unique, fun, and distinctive. Above all, it should be highly readable and easy to navigate.

These are the specific sections/categories of the blog that should be included and incorporated into the design SEE BELOW.

Thanks in advance for your consideration
Updates

Project Deadline Extended
Reason: I have extended the deadline to evaluate more designs from other pros

Hello all, Please take a minute to review the requirements for this project and please make sure you are capable of meeting ALL the requirements. As you already know I will be making a decision very shortly on whose design I will be moving forward with, if there are any last minute submissions now is the time. Thank you for your time.

Target Market(s)

90 % women 10 % men my clients are usually professionals who value their appearance, health, longevity and time.

Industry/Entity Type

Personal Trainer

Font styles to use
Serif

Colors
886aae
ffcf3e

Requirements
Must have
• Requirements

- start losing weight today.... 555 207 9184 (first line)
- visuals/images and backgrounds to give the idea of wellness, weight loss, healthy living, etc
- navigation menu - home, who we are, what we do, who we serve, blog, contact, members area

1) slider element at top below navigation menu
2) slider element near bottom of page will have testimonials
3) contact form/inquiry form (one page)
4) will provide wellness logo (to give credibility)
5) color scheme purple, gold and white
6) membership area
7) fb, tw, youtube icons
8) footer area - In the footer, there will be smaller company logo, copyright,
disclaimer, privacy policy, terms n conditions, verse of day, and contact info, Phone: (555) 207-9184
Email: support@...
Address:
9) use dummy content/graphic as they will be replaced by real content (the winner will provide instruction on how to make changes to all text and changing graphics)
9) ecommerce enabled / newsletter signup area

```html
<!DOCTYPE html>
<html lang="en">
<head>
<meta charset="utf-8">
<title>FitPennyCoach — Start Losing Weight Today</title>
<link rel="stylesheet" href="https://fonts.googleapis.com/css2?family=Montserrat:wght@400;600;700&family=Open+Sans:wght@400;600;700&display=swap">
<style>
  :root{
    --purple:#8a137f;
    --purple-dark:#6e0b65;
    --purple-light:#9c1e90;
    --page:#efefef;
    --card:#ffffff;
    --ink:#222222;
    --muted:#9a9a9a;
    --line:#e2e2e2;
    --footer:#262626;
    --footer-bottom:#1b1b1b;
    --footer-text:#8a8a8a;
    --social-blue:#5b74a8;
  }
  *{box-sizing:border-box;margin:0;padding:0}
  html,body{width:1200px;height:2375px;overflow:hidden}
  body{position:relative;background:var(--page);font-family:"Open Sans",Arial,sans-serif;color:var(--ink)}

  /* header */
  .site-header{position:absolute;left:0;top:0;width:1200px;height:70px;background:linear-gradient(180deg,var(--purple-light),var(--purple-dark))}
  .brand{position:absolute;left:55px;top:13px;display:flex;align-items:center;gap:12px}
  .brand-mark{width:40px;height:40px;border-radius:50%;border:2px solid #fff}
  .brand-name{font-family:"Open Sans",Arial,sans-serif;font-weight:700;font-size:23px;color:#fff;letter-spacing:.3px}
  .main-nav{position:absolute;right:20px;top:0;display:flex;height:70px}
  .main-nav a{display:block;height:70px;line-height:70px;padding:0 21px;color:#fff;font-size:13px;text-decoration:none}
  .main-nav a.current{background:rgba(0,0,0,.18)}

  /* hero */
  .hero{position:absolute;left:0;top:70px;width:1200px;height:429px;
    background:linear-gradient(90deg,#e9eaea 0%,#dcdcdb 30%,#c9c2bd 48%,#d98a72 62%,#e6b59a 75%,#efe5de 100%)}
  .hero-kicker{position:absolute;left:50px;top:108px;font-family:"Montserrat",Arial,sans-serif;font-size:20px;color:#222;letter-spacing:.3px}
  .hero-title{position:absolute;left:47px;top:132px;font-family:"Montserrat",Arial,sans-serif;font-weight:700;font-size:73px;color:#1d1d1d;letter-spacing:0;line-height:1}
  .hero-sub{position:absolute;left:50px;top:218px;font-family:"Montserrat",Arial,sans-serif;font-weight:700;font-size:21px;color:#1d1d1d}
  .slider-dots{position:absolute;left:558px;top:408px;width:84px;height:18px;border-radius:9px;background:rgba(80,40,40,.55);display:flex;justify-content:center;align-items:center;gap:6px}
  .slider-dots span{width:9px;height:9px;border-radius:50%;border:1.5px solid #fff}
  .slider-dots span.on{background:#fff}

  /* articles */
  .section-title{position:absolute;left:52px;top:540px;font-family:"Montserrat",Arial,sans-serif;font-weight:600;font-size:31px;color:var(--purple)}
  .article{position:absolute;left:52px;width:771px;height:317px;background:var(--card);border-radius:3px}
  .article-thumb{position:absolute;left:14px;top:14px;width:355px;height:283px}
  .article-title{position:absolute;left:401px;top:20px;width:350px;font-size:16.5px;line-height:21px;font-weight:400;color:#222}
  .article-meta{position:absolute;left:401px;top:78px;display:flex;gap:28px;font-size:11.5px;color:#b5b5b5}
  .article-meta span{display:flex;align-items:center;gap:6px}
  .article-meta svg{fill:#c5c5c5}
  .article-excerpt{position:absolute;left:401px;top:114px;width:350px;font-size:11px;line-height:20.5px;color:#9a9a9a}
  .read-more{position:absolute;left:403px;top:252px;width:72px;height:25px;border-radius:3px;background:linear-gradient(#f3f3f3,#d2d2d2);border:1px solid #c4c4c4;font-size:10.5px;line-height:23px;text-align:center;color:#333}

  /* pagination */
  .pagination{position:absolute;left:52px;top:1996px;display:flex;gap:9px}
  .pagination span{height:24px;min-width:24px;padding:0 7px;background:#fff;border:1px solid #d8d8d8;border-radius:2px;font-size:11px;line-height:22px;text-align:center;color:#444;font-weight:600}

  /* sidebar */
  .sidebar{position:absolute;left:879px;top:548px;width:267px;height:1415px;background:#fff;border-radius:3px}
  .widget-title{position:absolute;left:17px;font-size:13.5px;color:var(--purple);font-weight:600}
  .widget-note{position:absolute;left:17px;top:40px;width:230px;font-size:9px;line-height:12px;color:#aaa}
  .field{position:absolute;left:17px;width:223px;border:1px solid #e0e0e0;font-size:9.5px;color:#444;padding:12px 8px}
  .submit{position:absolute;left:19px;top:299px;width:56px;height:30px;background:#2e2e2e;border-radius:4px;color:#fff;font-size:9.5px;line-height:30px;text-align:center}
  .social-grid{position:absolute;left:17px;top:384px;width:230px;display:flex;flex-wrap:wrap;gap:3px}
  .social-grid span{width:21px;height:22px;background:#dcdcdc;border-radius:2px}
  .member{position:absolute;left:17px;width:230px;height:52px}
  .member-thumb{position:absolute;left:0;top:0;width:51px;height:51px}
  .member-title{position:absolute;left:61px;top:0;font-size:10.5px;color:#222}
  .member-date{position:absolute;left:61px;top:17px;font-size:10.5px;color:#444}
  .quote-mark{position:absolute;left:20px;top:830px}
  .testimonial{position:absolute;left:28px;top:861px;width:218px;font-size:11px;line-height:20.5px;text-align:center;color:#333}
  .testimonial-author{position:absolute;left:0;top:1102px;width:267px;text-align:center;font-size:11px;font-style:italic;color:#333}
  .social-box{position:absolute;left:17px;top:1196px;width:236px}
  .social-page-mark{position:absolute;left:0;top:0;width:42px;height:42px;background:var(--purple)}
  .social-page-name{position:absolute;left:52px;top:0;font-size:10px;color:var(--social-blue);font-weight:600}
  .social-like{position:absolute;left:52px;top:18px;width:40px;height:16px;background:var(--social-blue);border-radius:2px;color:#fff;font-size:9px;line-height:16px;text-align:center}
  .social-count{position:absolute;left:0;top:50px;font-size:9px;color:#444}
  .social-faces{position:absolute;left:0;top:81px;display:flex;flex-wrap:wrap;gap:2px;width:230px}
  .social-faces span{width:44px;height:43px}
  .social-plugin{position:absolute;left:0;top:186px;width:230px;border-top:1px solid #e2e2e2;padding-top:6px;font-size:8.5px;color:#777}

  /* footer */
  .site-footer{position:absolute;left:0;top:2050px;width:1200px;height:249px;background:var(--footer)}
  .footer-mark{position:absolute;left:55px;top:60px;width:54px;height:54px;border-radius:50%;border:2px solid #4a4a4a}
  .footer-col{position:absolute;top:40px}
  .footer-col h4{font-size:14px;font-weight:600;color:#fff;margin-bottom:18px;letter-spacing:.3px}
  .footer-col a{display:block;font-size:11.5px;line-height:20.5px;color:var(--footer-text);text-decoration:none}
  .footer-col p{font-size:11.5px;line-height:16px;color:var(--footer-text)}
  .newsletter{position:absolute;left:0;top:78px;width:279px;height:63px;display:flex}
  .newsletter-input{width:230px;height:63px;background:#fff;font-size:13px;line-height:63px;padding-left:18px;color:#222}
  .newsletter-btn{width:49px;height:63px;background:var(--purple);display:flex;align-items:center;justify-content:center}
  .contact-line{display:flex;align-items:flex-start;gap:12px;font-size:11.5px;line-height:15px;color:var(--footer-text);margin-bottom:18px}
  .contact-line svg{fill:#fff;flex:none}
  .footer-bottom{position:absolute;left:0;top:2299px;width:1200px;height:76px;background:var(--footer-bottom);text-align:center;font-size:11.5px;line-height:76px;color:#ddd}
</style>
</head>
<body>

<header class="site-header">
  <div class="brand"><span class="brand-mark"></span><span class="brand-name">FITPENNYCOACH</span></div>
  <nav class="main-nav">
    <a class="current" href="#">Home</a>
    <a href="#">Who we are</a>
    <a href="#">What we do</a>
    <a href="#">Who we serve</a>
    <a href="#">Contact</a>
    <a href="#">Blog</a>
    <a href="#">Members</a>
  </nav>
</header>

<section class="hero" role="img" aria-label="Slider photo: a tired woman in a coral top holding her hand to her forehead">
  <div class="hero-kicker">START LOSING</div>
  <div class="hero-title">WEIGHT</div>
  <div class="hero-sub">TODAY....</div>
  <div class="slider-dots"><span class="on"></span><span></span><span></span><span></span></div>
</section>

<h2 class="section-title">RECENT ARTICLES</h2>

<article class="article" style="top:606px">
  <div class="article-thumb" role="img" aria-label="Photo: smiling woman listening to music on headphones" style="background:linear-gradient(135deg,#b7cf6a,#d9c2a6 50%,#8a6a4a)"></div>
  <h3 class="article-title">50 Bloggers Making a Difference in Fitness, Health, and Happiness</h3>
  <div class="article-meta">
    <span><svg width="12" height="12" viewBox="0 0 12 12"><circle cx="6" cy="6" r="5.5" fill="none" stroke="#c5c5c5" stroke-width="1.5"/><path d="M6 3v3.5h2.5" fill="none" stroke="#c5c5c5" stroke-width="1.4"/></svg>08.02 , 2014</span>
    <span><svg width="14" height="12" viewBox="0 0 14 12"><ellipse cx="7" cy="5" rx="7" ry="5"/><path d="M3 9l-1 3 4-2z"/></svg>5 Comments</span>
    <span><svg width="15" height="12" viewBox="0 0 15 12"><path d="M9 0l6 5-6 5V7C4 7 1 9 0 12 0 6 3 3 9 3z"/></svg>Share</span>
  </div>
  <p class="article-excerpt">The Internet is a beautiful thing. Everyone and anyone can have a slice of the pie, which means there are hundreds of thousands (if not millions!) of blogs cropping up every day. The number of fitness, health, and happiness blogs out there can be overwhelming: How's an average Joe or Jane supposed to separate the good ones from the garbage (you know, those "blogs"</p>
  <div class="read-more">Read More</div>
</article>

<article class="article" style="top:951px">
  <div class="article-thumb" role="img" aria-label="Photo: smiling man in a white shirt working on a laptop" style="background:linear-gradient(135deg,#e4e8ea,#d8c3b0 45%,#f1f1f1)"></div>
  <h3 class="article-title">50 Bloggers Making a Difference in Fitness, Health, and Happiness</h3>
  <div class="article-meta">
    <span><svg width="12" height="12" viewBox="0 0 12 12"><circle cx="6" cy="6" r="5.5" fill="none" stroke="#c5c5c5" stroke-width="1.5"/><path d="M6 3v3.5h2.5" fill="none" stroke="#c5c5c5" stroke-width="1.4"/></svg>08.02 , 2014</span>
    <span><svg width="14" height="12" viewBox="0 0 14 12"><ellipse cx="7" cy="5" rx="7" ry="5"/><path d="M3 9l-1 3 4-2z"/></svg>5 Comments</span>
    <span><svg width="15" height="12" viewBox="0 0 15 12"><path d="M9 0l6 5-6 5V7C4 7 1 9 0 12 0 6 3 3 9 3z"/></svg>Share</span>
  </div>
  <p class="article-excerpt">The Internet is a beautiful thing. Everyone and anyone can have a slice of the pie, which means there are hundreds of thousands (if not millions!) of blogs cropping up every day. The number of fitness, health, and happiness blogs out there can be overwhelming: How's an average Joe or Jane supposed to separate the good ones from the garbage (you know, those "blogs"</p>
  <div class="read-more">Read More</div>
</article>

<article class="article" style="top:1298px">
  <div class="article-thumb" role="img" aria-label="Photo: slim waist wrapped with a measuring tape" style="background:linear-gradient(90deg,#a9c96a,#e1bfa3 35%,#f4f4f4 60%,#b9d37d)"></div>
  <h3 class="article-title">50 Bloggers Making a Difference in Fitness, Health, and Happiness</h3>
  <div class="article-meta">
    <span><svg width="12" height="12" viewBox="0 0 12 12"><circle cx="6" cy="6" r="5.5" fill="none" stroke="#c5c5c5" stroke-width="1.5"/><path d="M6 3v3.5h2.5" fill="none" stroke="#c5c5c5" stroke-width="1.4"/></svg>08.02 , 2014</span>
    <span><svg width="14" height="12" viewBox="0 0 14 12"><ellipse cx="7" cy="5" rx="7" ry="5"/><path d="M3 9l-1 3 4-2z"/></svg>5 Comments</span>
    <span><svg width="15" height="12" viewBox="0 0 15 12"><path d="M9 0l6 5-6 5V7C4 7 1 9 0 12 0 6 3 3 9 3z"/></svg>Share</span>
  </div>
  <p class="article-excerpt">The Internet is a beautiful thing. Everyone and anyone can have a slice of the pie, which means there are hundreds of thousands (if not millions!) of blogs cropping up every day. The number of fitness, health, and happiness blogs out there can be overwhelming: How's an average Joe or Jane supposed to separate the good ones from the garbage (you know, those "blogs"</p>
  <div class="read-more">Read More</div>
</article>

<article class="article" style="top:1646px">
  <div class="article-thumb" role="img" aria-label="Photo: man behind a large glass of beer" style="background:linear-gradient(90deg,#e0962a,#f2b64a 35%,#9a8a80 60%,#3a3a3a)"></div>
  <h3 class="article-title">50 Bloggers Making a Difference in Fitness, Health, and Happiness</h3>
  <div class="article-meta">
    <span><svg width="12" height="12" viewBox="0 0 12 12"><circle cx="6" cy="6" r="5.5" fill="none" stroke="#c5c5c5" stroke-width="1.5"/><path d="M6 3v3.5h2.5" fill="none" stroke="#c5c5c5" stroke-width="1.4"/></svg>08.02 , 2014</span>
    <span><svg width="14" height="12" viewBox="0 0 14 12"><ellipse cx="7" cy="5" rx="7" ry="5"/><path d="M3 9l-1 3 4-2z"/></svg>5 Comments</span>
    <span><svg width="15" height="12" viewBox="0 0 15 12"><path d="M9 0l6 5-6 5V7C4 7 1 9 0 12 0 6 3 3 9 3z"/></svg>Share</span>
  </div>
  <p class="article-excerpt">The Internet is a beautiful thing. Everyone and anyone can have a slice of the pie, which means there are hundreds of thousands (if not millions!) of blogs cropping up every day. The number of fitness, health, and happiness blogs out there can be overwhelming: How's an average Joe or Jane supposed to separate the good ones from the garbage (you know, those "blogs"</p>
  <div class="read-more">Read More</div>
</article>

<nav class="pagination">
  <span>Prev</span><span>1</span><span>2</span><span>3</span><span>4</span><span>5</span><span>6</span><span>...</span><span>22</span><span>Next</span>
</nav>

<aside class="sidebar">
  <h4 class="widget-title" style="top:16px">Contact us</h4>
  <p class="widget-note">subscribe to our monthly news updates in your mail address</p>
  <div class="field" style="top:82px;height:41px">Name</div>
  <div class="field" style="top:131px;height:41px">Email Id</div>
  <div class="field" style="top:180px;height:108px">Message</div>
  <div class="submit">SUBMIT</div>

  <h4 class="widget-title" style="top:350px">Get Connect With us</h4>
  <div class="social-grid">
    <span></span><span></span><span></span><span></span><span></span><span></span><span></span><span></span><span></span><span></span>
    <span></span><span></span><span></span><span></span><span></span>
  </div>

  <h4 class="widget-title" style="top:454px">Our Members</h4>
  <div class="member" style="top:497px"><div class="member-thumb" role="img" aria-label="Member portrait" style="background:#c99a80"></div><div class="member-title">Post with a Featured Image</div><div class="member-date">08 Aug , 2014</div></div>
  <div class="member" style="top:568px"><div class="member-thumb" role="img" aria-label="Member portrait" style="background:#b98466"></div><div class="member-title">Post with a Featured Image</div><div class="member-date">08 Aug , 2014</div></div>
  <div class="member" style="top:639px"><div class="member-thumb" role="img" aria-label="Member portrait" style="background:#b48a7c"></div><div class="member-title">Post with a Featured Image</div><div class="member-date">08 Aug , 2014</div></div>
  <div class="member" style="top:714px"><div class="member-thumb" role="img" aria-label="Member portrait" style="background:#a86a5c"></div><div class="member-title">Post with a Featured Image</div><div class="member-date">08 Aug , 2014</div></div>

  <h4 class="widget-title" style="top:799px">Testimonials</h4>
  <svg class="quote-mark" width="40" height="32" viewBox="0 0 40 32"><path fill="#d6d6d6" d="M0 32V18C0 8 5 2 15 0l2 4c-6 2-8 6-8 10h8v18zm22 0V18c0-10 5-16 15-18l2 4c-6 2-8 6-8 10h8v18z"/></svg>
  <p class="testimonial">&nbsp;&nbsp;&nbsp;&nbsp;&nbsp;&nbsp;&nbsp;&nbsp;Sed ut perspiciatis unde omnis iste natus error sit voluptatem accusantium doloremque laudantium, totam rem aperiam, eaque ipsa quae ab illo inventore veritatis et quasi architecto beatae vitae dicta sunt explicabo. Nemo enim ipsam voluptatem quia voluptas sit aspernatur aut odit aut fugit, sed quia consequuntur magni dolores eos qui ratione voluptatem sequi nesciunt.</p>
  <div class="testimonial-author">_Daniel Ross, NY-</div>

  <h4 class="widget-title" style="top:1168px">Circlepage</h4>
  <div class="social-box">
    <div class="social-page-mark"></div>
    <div class="social-page-name">fitpennycoach</div>
    <div class="social-like">Like</div>
    <div class="social-count">135 people like wellpathdaily.com</div>
    <div class="social-faces">
      <span role="img" aria-label="Fan photo" style="background:#8a8a8a"></span>
      <span role="img" aria-label="Fan photo" style="background:#7a3a3a"></span>
      <span role="img" aria-label="Fan photo" style="background:#6a7a4a"></span>
      <span role="img" aria-label="Fan photo" style="background:#a07a5a"></span>
      <span role="img" aria-label="Fan photo" style="background:#9a8aa0"></span>
      <span role="img" aria-label="Fan photo" style="background:#5a5a5a"></span>
      <span role="img" aria-label="Fan photo" style="background:#8a6a4a"></span>
      <span role="img" aria-label="Fan photo" style="background:#b09a6a"></span>
      <span role="img" aria-label="Fan photo" style="background:#6a6a7a"></span>
      <span role="img" aria-label="Fan photo" style="background:#7a5a4a"></span>
    </div>
    <div class="social-plugin">Circlepage social plugin</div>
  </div>
</aside>

<footer class="site-footer">
  <div class="footer-mark"></div>
  <div class="footer-col" style="left:152px">
    <h4>QUICK LINKS</h4>
    <a href="#">Home</a><a href="#">Who we are</a><a href="#">What we do</a><a href="#">Who we serve</a><a href="#">Contact</a><a href="#">Blog</a><a href="#">Members</a>
  </div>
  <div class="footer-col" style="left:326px">
    <h4>COMPANY</h4>
    <a href="#">privacy policy</a><a href="#">terms n conditions</a><a href="#">verse of day</a>
  </div>
  <div class="footer-col" style="left:494px;width:300px">
    <h4>SUBSCRIBE NEWSLETTER</h4>
    <p>Sed ut perspiciatis unde omnis iste natus error accusantium doloremque</p>
    <div class="newsletter">
      <div class="newsletter-input">Enter&nbsp; Your Mail Id</div>
      <div class="newsletter-btn"><svg width="18" height="22" viewBox="0 0 18 22"><path d="M3 2l10 9-10 9" fill="none" stroke="#fff" stroke-width="4"/></svg></div>
    </div>
  </div>
  <div class="footer-col" style="left:847px;width:300px">
    <h4>CONTACT INFO</h4>
    <div class="contact-line"><svg width="13" height="18" viewBox="0 0 13 18"><path d="M6.5 0A6.5 6.5 0 0 0 0 6.5C0 11 6.5 18 6.5 18S13 11 13 6.5A6.5 6.5 0 0 0 6.5 0zm0 9a2.5 2.5 0 1 1 0-5 2.5 2.5 0 0 1 0 5z"/></svg><span>Sed ut perspiciatis unde omnis iste natus error accusantium doloremque</span></div>
    <div class="contact-line"><svg width="18" height="12" viewBox="0 0 18 12"><rect x="0.75" y="0.75" width="16.5" height="10.5" fill="none" stroke="#fff" stroke-width="1.5"/><path d="M1 1l8 6 8-6" fill="none" stroke="#fff" stroke-width="1.5"/></svg><span>support@...</span></div>
    <div class="contact-line"><svg width="16" height="16" viewBox="0 0 16 16"><path d="M3 0l3 4-2 2c1 2 4 5 6 6l2-2 4 3-2 3C8 16 0 8 0 2z"/></svg><span>(555) 207-9184</span></div>
  </div>
</footer>
<div class="footer-bottom">© 2014 FitPennyCoach.com. All rights reserved.</div>

</body>
</html>
```